Moxy Fen needs some awesome stationary

Do you have what it takes to get my brand? You either do or you don't, have a crack at a design and you my just win my business.

I don't want to waste your or my time, so put your creative genius on either a business card or envelope.

I however need a package of stationary that follows the same brand. I will message you to complete the remaining should I like your first submission.

Here is what I need, have a go!

Basically I need the following for my small business based in melbourne.
- Letterhead (printer ready and MS Word)
- Business Card
- Compliments Slip
- Envelope
- Proposal Cover Page (MS Word only)
- Presentation Folder
- Marbled Fox Cards
- Student Name Tent
- Index Cards
- Vell-Ka

I am establishing the brand and it must be modern, professional but also relaxed; that is not formal and not corporate. It represents a company are leaders, but small enough to care and operate like a bunch of friends. We are bringing people and conversations back to business, and turfing out all the bureaucracy and crazy and wasteful procedures. Its about "lets talk and figure it out together and find even better ways".

Target Market(s)

Mainly companies that build software products, but Agile practices are used in many other industries (even graphic design projects)

Industry/Entity Type

Information Technology

Font styles to use
Sans Serif

Colors
3176b5
aaaaaa

Requirements
Must have
• I like curves and circles and not boxes or rectangles.
• I want a colour rich design with my brand colours, but it must be balanced.
• I want more modern than traditional, but simple modern
Should not have
• Not corporate
• Please don't waste my time if your not going to think about it.
• Don't mess with my primary logo
• Don't change my colours
• Don't overlay logo on image

```html
<!DOCTYPE html>
<html lang="en">
<head>
<meta charset="utf-8">
<title>Moxy Fen – Business Card</title>
<link rel="stylesheet" href="https://fonts.googleapis.com/css2?family=Nunito:wght@800&family=PT+Sans+Narrow:wght@400;700&family=Syncopate:wght@700&display=swap">
<style>
  :root {
    --brand-blue: #3176b5;
    --brand-blue-deep: #1d5fae;
    --brand-grey: #aaaaaa;
    --card-grey-dark: #9aa3b5;
    --card-grey-light: #c9ced8;
    --paper: #ffffff;
    --ink: #2b3a55;
    --stage: #b9cde0;
  }
  * { box-sizing: border-box; margin: 0; padding: 0; }
  html, body { width: 1200px; height: 800px; overflow: hidden; }
  body {
    background: var(--stage);
    display: flex;
    align-items: center;
    justify-content: center;
    gap: 40px;
  }
  .card {
    position: relative;
    width: 540px;
    height: 309px;
    overflow: hidden;
    box-shadow: 0 4px 14px rgba(40, 60, 90, 0.18);
  }
  .card__tab {
    position: absolute;
    left: 0;
    top: 150px;
    width: 5px;
    height: 60px;
    background: var(--brand-blue-deep);
  }

  /* Front */
  .card--front { background: var(--card-grey-dark); }
  .card__texture {
    position: absolute;
    inset: 0;
    background: linear-gradient(115deg, var(--card-grey-dark) 0%, var(--card-grey-light) 45%, #b3bac8 60%, var(--card-grey-dark) 100%);
  }
  .front-brand {
    position: absolute;
    left: 150px;
    top: 108px;
    display: flex;
    align-items: center;
    gap: 14px;
  }
  .brand-dot {
    width: 46px;
    height: 46px;
    border-radius: 50%;
    background: var(--brand-blue-deep);
  }
  .brand-name {
    font-family: "Nunito", sans-serif;
    font-weight: 800;
    font-size: 40px;
    color: var(--brand-blue-deep);
    line-height: 1;
  }
  .front-url {
    position: absolute;
    left: 210px;
    top: 168px;
    font-family: "PT Sans Narrow", sans-serif;
    font-size: 20px;
    color: var(--paper);
    letter-spacing: 0.5px;
  }

  /* Back */
  .card--back { background: var(--paper); }
  .back-brand {
    position: absolute;
    left: 36px;
    top: 118px;
    width: 200px;
  }
  .back-brand__row { display: flex; align-items: center; gap: 10px; }
  .back-brand .brand-dot { width: 34px; height: 34px; }
  .back-brand .brand-name { font-size: 31px; }
  .back-brand__rule {
    height: 1.5px;
    background: var(--brand-blue-deep);
    margin: 7px 0 5px;
  }
  .back-brand__legal {
    font-family: "Nunito", sans-serif;
    font-weight: 800;
    font-size: 16px;
    color: var(--brand-blue-deep);
    padding-left: 20px;
  }
  .card__divider {
    position: absolute;
    left: 262px;
    top: 30px;
    bottom: 30px;
    width: 1px;
    background: #d9dde4;
  }
  .contact {
    position: absolute;
    left: 286px;
    top: 62px;
    font-family: "PT Sans Narrow", sans-serif;
    color: var(--ink);
  }
  .contact__name {
    font-family: "Syncopate", sans-serif;
    font-weight: 700;
    font-size: 15px;
    color: var(--brand-blue-deep);
    letter-spacing: 1px;
  }
  .contact__title { font-size: 11px; margin: 2px 0 12px; }
  .contact__list { list-style: none; }
  .contact__item {
    display: flex;
    align-items: flex-start;
    gap: 9px;
    font-size: 16px;
    line-height: 1.3;
    margin-bottom: 6px;
  }
  .contact__item strong { font-weight: 700; }
  .contact__icon { flex: none; width: 16px; height: 16px; margin-top: 2px; }
</style>
</head>
<body>

  <section class="card card--front" aria-label="Business card front">
    <div class="card__texture" role="img" aria-label="Soft silver-grey background with a repeating tone-on-tone pattern"></div>
    <span class="card__tab"></span>
    <div class="front-brand">
      <span class="brand-dot"></span>
      <span class="brand-name">Moxy Fen</span>
    </div>
    <p class="front-url">www.moxy-fen.com.au</p>
  </section>

  <section class="card card--back" aria-label="Business card back">
    <span class="card__tab"></span>
    <div class="back-brand">
      <div class="back-brand__row">
        <span class="brand-dot"></span>
        <span class="brand-name">Moxy Fen</span>
      </div>
      <div class="back-brand__rule"></div>
      <p class="back-brand__legal">Moxy Fen Pty Ltd</p>
    </div>
    <span class="card__divider"></span>
    <div class="contact">
      <h1 class="contact__name">DANA COLVERY</h1>
      <p class="contact__title">CEO, Professional Agile Coach</p>
      <ul class="contact__list">
        <li class="contact__item">
          <svg class="contact__icon" viewBox="0 0 16 16"><circle cx="8" cy="8" r="7.3" fill="none" stroke="#3176b5" stroke-width="1.2"/><path d="M8 3.8a2.6 2.6 0 0 0-2.6 2.6C5.4 8.4 8 12 8 12s2.6-3.6 2.6-5.6A2.6 2.6 0 0 0 8 3.8z" fill="#3176b5"/><circle cx="8" cy="6.4" r="1" fill="#fff"/></svg>
          <span>PO Box 4410, Ashvale North,<br>VIC 3190, Australia</span>
        </li>
        <li class="contact__item">
          <svg class="contact__icon" viewBox="0 0 16 16"><circle cx="8" cy="8" r="7.3" fill="none" stroke="#3176b5" stroke-width="1.2"/><path d="M5.3 4.3l1.4-.4 1 2-1 .8c.4 1 1.1 1.7 2.1 2.1l.8-1 2 1-.4 1.4c-3 .2-6-2.8-5.9-5.9z" fill="#3176b5"/></svg>
          <strong>1300MOXYF</strong>
        </li>
        <li class="contact__item">
          <svg class="contact__icon" viewBox="0 0 16 16"><circle cx="8" cy="8" r="7.3" fill="none" stroke="#3176b5" stroke-width="1.2"/><rect x="5.6" y="3.8" width="4.8" height="8.4" rx="0.8" fill="#3176b5"/><rect x="6.4" y="5" width="3.2" height="5.4" fill="#fff"/></svg>
          <span>+61 400 123 987</span>
        </li>
        <li class="contact__item">
          <svg class="contact__icon" viewBox="0 0 16 16"><circle cx="8" cy="8" r="7.3" fill="none" stroke="#3176b5" stroke-width="1.2"/><rect x="4.2" y="5.3" width="7.6" height="5.4" fill="none" stroke="#3176b5" stroke-width="1"/><path d="M4.2 5.3L8 8.4l3.8-3.1" fill="none" stroke="#3176b5" stroke-width="1"/></svg>
          <span>dana@moxy-fen.com.au</span>
        </li>
      </ul>
    </div>
  </section>

</body>
</html>
```